Federal Government Proposal Development Consulting company needs a website designed and coded

I am looking for someone to design (using an existing logo, color palette, and text fonts) and code a wordpress-based website for a Proposal Development consulting company. I have full copy for all site pages and suggestions for images/ graphics and a few example design templates to go from.

One note, from a color perspective - I included a mockup of a business card to highlight a color scheme that I tend to like - if you look at the back of the business card, the blend of the grey, blue, with the neon green highlight as a separator really seems to pop. Just a thought as you are designing the page.

I would like to see 2-3 potential design layouts, and I will select one to move forward with. Then, I would like the site to be coded for WordPress (I can provide a login to my wordpress site). I would like 1 opportunity to review the coded site and make any final tweaks.

```html
<!DOCTYPE html>
<html lang="en">
<head>
<meta charset="utf-8">
<title>Bright Quill Consulting LLC</title>
<link href="https://fonts.googleapis.com/css2?family=Outfit:wght@500;600;700&family=Roboto:wght@400;500;700&display=swap" rel="stylesheet">
<style>
:root{
  --blue:#0a3fc7;
  --blue-deep:#06248a;
  --navy:#0b1733;
  --ink:#1a1d24;
  --text:#555b66;
  --muted:#8a8f99;
  --line:#e6e8ee;
  --white:#ffffff;
  --dark:#121212;
  --star:#f4b400;
}
*{margin:0;padding:0;box-sizing:border-box}
html,body{width:1200px;height:5172px;overflow:hidden}
body{position:relative;background:var(--white);font-family:"Roboto",sans-serif;color:var(--text)}
.abs{position:absolute}
.heading{font-family:"Outfit",sans-serif;font-weight:700;color:var(--ink);letter-spacing:1px}
.center{left:0;width:1200px;text-align:center}
.btn{position:absolute;display:flex;align-items:center;justify-content:center;height:44px;border-radius:22px;font:500 14px "Roboto",sans-serif}
.btn-white{background:var(--white);color:var(--ink)}
.btn-ghost{border:2px solid var(--white);color:var(--white)}
.btn-blue{background:var(--blue-deep);color:var(--white)}
.btn-outline{border:2px solid var(--blue-deep);color:var(--ink)}
.brand{font-family:"Outfit",sans-serif;font-weight:500;color:#7d8794;line-height:1.05}
.brand b{font-weight:500;display:block}
.contact{display:flex;align-items:center;gap:16px}
.contact .dot{width:42px;height:42px;border-radius:50%;background:var(--blue-deep);display:flex;align-items:center;justify-content:center}
.contact small{display:block;font-size:10px;color:var(--ink)}
.contact strong{display:block;font:500 17px "Roboto",sans-serif;color:var(--ink)}
.nav{display:flex;font-size:15px;color:var(--white)}
.photo{position:absolute}
.body-copy{font-size:13px;line-height:30px;color:var(--text)}
.card{position:absolute;top:1300px;width:314px;height:425px;background:var(--white);border-radius:14px;box-shadow:0 4px 24px rgba(0,0,0,.12);padding:24px 22px}
.card h3{font:600 17px "Outfit",sans-serif;color:var(--ink);margin:14px 0 8px}
.card p{font-size:12px;line-height:25px;color:var(--text);margin-bottom:24px}
.list{list-style:none;font-size:13px;line-height:30px;color:var(--text)}
.list li{padding-left:24px;position:relative}
.list li::before{content:"»";position:absolute;left:0;color:var(--blue-deep);font-weight:700}
.grid{position:absolute;left:110px;top:2940px;display:grid;grid-template-columns:repeat(4,244px);grid-auto-rows:216px}
.cell{border:1px solid var(--line);box-shadow:0 2px 10px rgba(0,0,0,.05);display:flex;flex-direction:column;align-items:center;justify-content:center;gap:22px;font:500 14px "Roboto",sans-serif;color:#4a4f59}
.field{position:absolute;background:var(--white);padding:0 36px;display:flex;align-items:center;font-size:14px;color:var(--text)}
.review{position:absolute;top:4660px;height:218px;background:var(--white);border-radius:10px;box-shadow:0 4px 20px rgba(0,0,0,.1);padding:26px 36px;font-size:12px;line-height:23px;color:var(--text)}
.reviewer{display:flex;align-items:center;gap:14px;margin-top:10px}
.avatar{width:44px;height:44px;border-radius:50%;background:#d8dce4}
.reviewer .name{color:var(--blue-deep);font-weight:700;font-size:13px}
.stars{color:var(--star);font-size:11px;letter-spacing:1px}
.arrow{position:absolute;top:4764px;width:30px;height:30px;border-radius:50%;display:flex;align-items:center;justify-content:center}
</style>
</head>
<body>

<!-- Header -->
<header>
  <div class="abs brand" style="left:110px;top:26px;font-size:30px"><b>Bright Quill</b><span style="font-size:15px;padding-left:44px">Consulting LLC</span></div>
  <div class="abs contact" style="left:570px;top:20px">
    <span class="dot"><svg width="18" height="14" viewBox="0 0 18 14"><rect x="1" y="1" width="16" height="12" rx="1.5" fill="none" stroke="#fff" stroke-width="2"/><path d="M1 2l8 6 8-6" fill="none" stroke="#fff" stroke-width="2"/></svg></span>
    <div><small>Email Us:</small><strong>info@BrightQuillGroup.com</strong></div>
  </div>
  <div class="abs contact" style="left:890px;top:20px">
    <span class="dot"><svg width="18" height="18" viewBox="0 0 24 24"><path fill="#fff" d="M6.6 10.8a15 15 0 006.6 6.6l2.2-2.2c.3-.3.7-.4 1-.2 1.1.4 2.3.6 3.6.6.6 0 1 .4 1 1V20c0 .6-.4 1-1 1A17 17 0 013 4c0-.6.4-1 1-1h3.5c.6 0 1 .4 1 1 0 1.3.2 2.5.6 3.6.1.3 0 .7-.2 1z"/></svg></span>
    <div><small>Call Us:</small><strong>(410) 555-0142</strong></div>
  </div>
  <svg class="abs" style="left:0;top:84px" width="1200" height="56"><path d="M392 0H1200V48H374Z" fill="#0a3fc7"/><rect x="0" y="51" width="1200" height="3" fill="#0a3fc7"/></svg>
  <nav class="abs nav" style="left:438px;top:100px;gap:0">
    <span style="width:120px">Home</span><span style="width:170px">Work With Us</span><span style="width:156px">Work For Us</span><span style="width:136px">About Us</span><span>Contact Us</span>
  </nav>
</header>

<!-- Hero -->
<section>
  <div class="photo" role="img" aria-label="Hands using a glowing digital dashboard with business charts" style="left:0;top:140px;width:1200px;height:532px;background:radial-gradient(circle at 74% 42%,#1f8fd6 0%,#0c3a6e 22%,#061325 52%,#02060d 100%)"></div>
  <h1 class="abs heading" style="left:108px;top:288px;font-size:52px;color:var(--white);letter-spacing:1.5px">GENERATE SUCCESS</h1>
  <p class="abs" style="left:108px;top:370px;width:440px;font-size:16px;line-height:38px;color:var(--white)">Fuel Innovation in Proposal Excellence with Bright Quill! <u>Click here</u> to explore our services.</p>
  <span class="btn btn-white" style="left:108px;top:470px;width:128px;height:42px">Get Started</span>
</section>

<!-- What we do -->
<section>
  <h2 class="abs heading center" style="top:752px;font-size:40px">WHAT WE DO</h2>
  <p class="abs body-copy" style="left:160px;top:820px;width:880px;text-align:center">Bright Quill, specializes in advancing an organization through a comprehensive suite of services designed to modernize the proposal development process. From innovative Capture Management strategies that pinpoint lucrative opportunities, meticulous Proposal Development services that transform concepts into effective narratives, and cutting-edge Generative AI techniques that create domain-aware content accelerating proposal draft development, we are your dedicated partner in securing success.</p>
  <div class="photo" role="img" aria-label="Blue digital wireframe of a skyscraper" style="left:0;top:994px;width:550px;height:628px;background:linear-gradient(135deg,#0a4fa8,#0d6ad0 50%,#062e78)"></div>
  <div class="abs body-copy" style="left:622px;top:1002px;width:470px">
    <p style="margin-bottom:30px">With a unique fusion of technical expertise and exceptional writing capabilities, we surpass industry standards and set new benchmarks for excellence.</p>
    <p>Discover a dynamic approach to proposal consulting that goes beyond conventional boundaries—choose Bright Quill for solutions that Enhance the quality of your work, Elevate your corporate advantage, and Expand your industry presence.</p>
  </div>
  <article class="card" style="left:104px">
    <svg width="64" height="62" viewBox="0 0 64 62" fill="none" stroke="#0a3fc7" stroke-width="2"><rect x="4" y="4" width="30" height="40" rx="2"/><path d="M10 14h18M10 22h18M10 30h12"/><rect x="30" y="30" width="30" height="26" rx="2"/><path d="M36 50V42M42 50V38M48 50V44M54 50V36"/></svg>
    <h3>Capture Management</h3>
    <p>Elevate your business development strategy with our Capture Management services. From opportunity identification to strategic planning, our experts will guide you through a meticulous process, ensuring the pursuit of the right contracts to position your organization for success.</p>
    <p>Trust us to analyze the market, mitigate risks, and develop strategies that maximize the ability to secure lucrative opportunities.</p>
  </article>
  <article class="card" style="left:442px">
    <svg width="64" height="62" viewBox="0 0 64 62" fill="none" stroke="#0a3fc7" stroke-width="2"><rect x="4" y="14" width="30" height="38" rx="2"/><path d="M10 24h16M10 32h16M10 40h10"/><circle cx="40" cy="34" r="12"/><path d="M49 43l10 10"/><circle cx="48" cy="12" r="6"/></svg>
    <h3>Proposal Development</h3>
    <p>Transform your vision into winning proposals with our Proposal Development services. We specialize in persuasive narratives, clear technical solutions, and strategic pricing models. From meticulous compliance reviews to captivating executive summaries, we ensure every aspect of a proposal is polished and aligned with your objectives.</p>
    <p>Turn your ideas into persuasive documents that leave a lasting impression</p>
  </article>
  <article class="card" style="left:782px">
    <svg width="64" height="62" viewBox="0 0 64 62" fill="none" stroke="#0a3fc7" stroke-width="2"><path d="M30 6c-12 0-20 8-20 18 0 6 3 10 3 14 0 6 6 12 17 12"/><path d="M30 6c12 0 20 8 20 18 0 6-3 10-3 14 0 6-6 12-17 12"/><circle cx="22" cy="22" r="3"/><circle cx="38" cy="22" r="3"/><circle cx="30" cy="34" r="3"/><path d="M22 22l8 12 8-12"/></svg>
    <h3>Generative AI</h3>
    <p>Revolutionize your proposal writing process with our domain-aware Generative AI services. Using customer-installed tools, we leverage domain-aware artificial intelligence to generate innovative and tailored proposal content. This not only accelerates the proposal development timeline but also ensures content that is both dynamic and targeted.</p>
    <p>Stay ahead of the curve with proposals that not only meet industry standards</p>
  </article>
</section>

<!-- Who we are -->
<section>
  <div class="photo" role="img" aria-label="Blue technology background with faint digital interface" style="left:0;top:1828px;width:1200px;height:382px;background:linear-gradient(180deg,#0a2a8c,#0b3fc4 60%,#0a46d6)"></div>
  <h2 class="abs heading center" style="top:1898px;font-size:40px;color:var(--white)">WHO WE ARE</h2>
  <p class="abs" style="left:150px;top:1968px;width:900px;text-align:center;font-size:13px;line-height:29px;color:var(--white)">Sed ut perspiciatis unde omnis iste natus error sit voluptatem accusantium doloremque laudantium, totam rem aperiam, eaque ipsa quae ab illo inventore veritatis et quasi architecto beatae vitae dicta sunt explicabo. Nemo enim ipsam voluptatem quia voluptas sit aspernatur aut odit aut fugit, sed quia consequuntur magni dolores eos qui ratione voluptatem sequi nesciunt.</p>
  <span class="btn btn-white" style="left:472px;top:2086px;width:120px">View More</span>
  <span class="btn btn-ghost" style="left:608px;top:2086px;width:122px">Get Started</span>
</section>

<!-- Subject matter expertise -->
<section>
  <h2 class="abs heading" style="left:108px;top:2310px;font-size:40px;line-height:54px">SUBJECT<br>MATTER EXPERTISE</h2>
  <ul class="abs list" style="left:110px;top:2438px;width:240px">
    <li>Generative AI</li><li>Software/ Hardware Engineering</li><li>Systems Engineering</li><li>High-Performance Computing (HPC)</li><li>Logistics</li><li>Warehousing</li>
  </ul>
  <ul class="abs list" style="left:368px;top:2438px;width:240px">
    <li>Information Technology Support</li><li>Cybersecurity</li><li>Data Analysis</li><li>Systems Integration</li><li>Program Management</li><li>Systems Development &amp; Testing</li><li>Secure Supply Chain (ISO 28000 &amp; ISO 20243-1)</li>
  </ul>
  <span class="btn btn-blue" style="left:110px;top:2696px;width:130px;height:40px">Get Started</span>
  <div class="photo" role="img" aria-label="Engineer working at monitors in a server room" style="left:642px;top:2312px;width:472px;height:434px;border-radius:16px;background:linear-gradient(135deg,#1b3f7a,#0d2248 55%,#071226)"></div>
</section>

<!-- Services -->
<section>
  <h2 class="abs heading center" style="top:2846px;font-size:40px">OUR SERVICES</h2>
  <div class="grid">
    <div class="cell"><svg width="64" height="64" viewBox="0 0 64 64" fill="none" stroke="#222" stroke-width="2"><ellipse cx="32" cy="32" rx="28" ry="11"/><ellipse cx="32" cy="32" rx="28" ry="11" transform="rotate(60 32 32)"/><ellipse cx="32" cy="32" rx="28" ry="11" transform="rotate(-60 32 32)"/><text x="32" y="37" text-anchor="middle" font-size="14" font-family="Roboto" fill="#222" stroke="none">AI</text></svg>Generative AI</div>
    <div class="cell"><svg width="64" height="64" viewBox="0 0 64 64" fill="none" stroke="#222" stroke-width="2"><path d="M10 54l26-26M14 58l26-26"/><circle cx="46" cy="18" r="10"/><path d="M12 8l8 8-4 4-8-8zM20 16l34 34-4 4-34-34"/></svg>Technical Solutioning</div>
    <div class="cell"><svg width="64" height="64" viewBox="0 0 64 64" fill="none" stroke="#222" stroke-width="2"><rect x="6" y="4" width="30" height="40" rx="2"/><path d="M12 14h18M12 22h18M12 30h12"/><rect x="30" y="32" width="30" height="26" rx="2"/><path d="M36 52v-8M42 52v-12M48 52v-6M54 52v-14"/></svg>Capture Management</div>
    <div class="cell"><svg width="64" height="64" viewBox="0 0 64 64" fill="none" stroke="#222" stroke-width="2"><rect x="6" y="6" width="34" height="46" rx="2"/><path d="M12 18h22M12 26h22M12 34h22M12 42h14"/><rect x="38" y="30" width="20" height="24" rx="2"/><path d="M42 38h12M42 46h12"/></svg>Proposal Management</div>
    <div class="cell"><svg width="64" height="64" viewBox="0 0 64 64" fill="none" stroke="#222" stroke-width="2"><rect x="6" y="6" width="52" height="22" rx="3"/><path d="M16 13l2 4h4l-3 3 1 4-4-2-4 2 1-4-3-3h4zM32 13l2 4h4l-3 3 1 4-4-2-4 2 1-4-3-3h4zM48 13l2 4h4l-3 3 1 4-4-2-4 2 1-4-3-3h4z"/><path d="M22 58V40a4 4 0 018 0v6h8a4 4 0 014 4v8"/><rect x="12" y="42" width="8" height="16"/></svg>Compliance Reviews</div>
    <div class="cell"><svg width="64" height="64" viewBox="0 0 64 64" fill="none" stroke="#222" stroke-width="2"><rect x="24" y="6" width="32" height="42" rx="2"/><path d="M30 38v-6M36 38v-12M42 38v-8M48 38v-16"/><path d="M6 58l12-12 8 4"/><path d="M10 50l8-10 8 2"/></svg>Executive Summaries</div>
    <div class="cell"><svg width="64" height="64" viewBox="0 0 64 64" fill="none" stroke="#222" stroke-width="2"><path d="M8 58V48h8v10M22 58V40h8v18M36 58V32h8v26M50 58V22h8v36"/><path d="M8 36L28 22l10 6 20-18"/><path d="M50 10h8v8"/></svg>Volume Lead</div>
    <div class="cell"><svg width="64" height="64" viewBox="0 0 64 64" fill="none" stroke="#222" stroke-width="2"><rect x="6" y="6" width="44" height="52" rx="2"/><path d="M6 16h44M14 26h12v10H14zM32 26h12M32 32h12M14 44h30M14 50h22"/><path d="M58 18l-14 30-4 4 0-6 14-30z"/></svg>Technical Writer</div>
    <div class="cell"><svg width="64" height="64" viewBox="0 0 64 64" fill="none" stroke="#222" stroke-width="2.5"><circle cx="30" cy="34" r="24"/><path d="M30 34V10M30 34l20 14"/><path d="M36 6a24 24 0 0122 22H36z"/></svg>Gantt Charts</div>
    <div class="cell"><svg width="64" height="64" viewBox="0 0 64 64" fill="none" stroke="#222" stroke-width="2"><circle cx="18" cy="18" r="10"/><path d="M25 25l10 10"/><path d="M36 56V40h6v16M46 56V30h6v26M56 56V20h6v36"/><path d="M6 58h58"/></svg>Market Survey</div>
    <div class="cell"><svg width="64" height="64" viewBox="0 0 64 64" fill="none" stroke="#222" stroke-width="2"><rect x="4" y="16" width="40" height="28" rx="2"/><path d="M18 52h12M24 44v8"/><rect x="46" y="8" width="14" height="46" rx="2"/><path d="M50 16h6M50 22h6"/></svg>Desktop Publishing</div>
    <div class="cell"><svg width="64" height="64" viewBox="0 0 64 64" fill="none" stroke="#222" stroke-width="2"><circle cx="32" cy="32" r="8"/><circle cx="32" cy="8" r="5"/><circle cx="32" cy="56" r="5"/><circle cx="10" cy="20" r="5"/><circle cx="54" cy="20" r="5"/><circle cx="10" cy="44" r="5"/><circle cx="54" cy="44" r="5"/><path d="M32 13v11M32 40v11M14 22l11 6M50 22l-11 6M14 42l11-6M50 42l-11-6"/></svg>Color Team Reviewer</div>
  </div>
  <span class="btn btn-blue" style="left:462px;top:3622px;width:128px">View More</span>
  <span class="btn btn-outline" style="left:608px;top:3622px;width:130px">Get Started</span>
</section>

<!-- Contact -->
<section>
  <div class="photo" role="img" aria-label="Blue digital globe and network background" style="left:0;top:3756px;width:1200px;height:704px;background:radial-gradient(circle at 50% 35%,#1c63e8,#0b3fc4 55%,#0838b0)"></div>
  <h2 class="abs heading center" style="top:3828px;font-size:40px;color:var(--white)">GET IN TOUCH WITH US</h2>
  <p class="abs center" style="top:3890px;font-size:15px;color:var(--white)">At vero eos et accusamus et iusto odio dignissimos ducimus qui blanditiis praesentium voluptatum</p>
  <div class="field" style="left:152px;top:3952px;width:432px;height:56px">First Name</div>
  <div class="field" style="left:616px;top:3952px;width:432px;height:56px">Last Name</div>
  <div class="field" style="left:152px;top:4040px;width:432px;height:56px">Contact Number</div>
  <div class="field" style="left:616px;top:4040px;width:432px;height:56px">Email Address</div>
  <div class="field" style="left:152px;top:4126px;width:896px;height:176px;align-items:flex-start;padding-top:22px">Message</div>
  <span class="btn btn-ghost" style="left:536px;top:4342px;width:128px;height:40px">Submit Now</span>
</section>

<!-- Testimonials -->
<section>
  <h2 class="abs heading center" style="top:4534px;font-size:40px">OUR HAPPY CUSTOMERS</h2>
  <p class="abs center" style="top:4604px;font-size:14px;color:var(--text)">At vero eos et accusamus et iusto odio dignissimos ducimus qui blanditiis praesentium voluptatum deleniti atque</p>
  <span class="arrow" style="left:58px;background:#c9d3ea"><svg width="10" height="10" viewBox="0 0 10 10"><path d="M7 1L3 5l4 4" fill="none" stroke="#fff" stroke-width="2"/></svg></span>
  <span class="arrow" style="left:1112px;background:var(--blue)"><svg width="10" height="10" viewBox="0 0 10 10"><path d="M3 1l4 4-4 4" fill="none" stroke="#fff" stroke-width="2"/></svg></span>
  <div class="review" style="left:116px;width:456px">
    <p>At vero eos et accusamus et iusto odio dignissimos ducimus qui blanditiis praesentium voluptatum deleniti atque corrupti quos dolores et quas molestias excepturi sint occaecati cupiditate non provident, similique sunt in culpa qui officia</p>
    <div class="reviewer"><span class="avatar"></span><div><div class="stars">★★★★★</div><div class="name">Daniel Reyes</div></div></div>
  </div>
  <div class="review" style="left:616px;width:466px">
    <p>At vero eos et accusamus et iusto odio dignissimos ducimus qui blanditiis praesentium voluptatum deleniti atque corrupti quos dolores et quas molestias excepturi sint occaecati cupiditate non provident, similique sunt in culpa qui officia</p>
    <div class="reviewer"><span class="avatar"></span><div><div class="stars">★★★★★</div><div class="name">Daniel Reyes</div></div></div>
  </div>
</section>

<!-- Footer -->
<footer>
  <div class="abs" style="left:0;top:4930px;width:1200px;height:242px;background:var(--dark)"></div>
  <div class="abs brand" style="left:110px;top:5010px;font-size:40px;color:#9aa3ae"><b>Bright Quill</b><span style="font-size:20px;padding-left:60px">Consulting LLC</span></div>
  <div class="abs contact" style="left:570px;top:5002px">
    <span class="dot" style="background:var(--white)"><svg width="18" height="14" viewBox="0 0 18 14"><rect x="1" y="1" width="16" height="12" rx="1.5" fill="none" stroke="#06248a" stroke-width="2"/><path d="M1 2l8 6 8-6" fill="none" stroke="#06248a" stroke-width="2"/></svg></span>
    <div><small style="color:#fff">Email Us:</small><strong style="color:#fff">info@BrightQuillGroup.com</strong></div>
  </div>
  <div class="abs contact" style="left:890px;top:5002px">
    <span class="dot" style="background:var(--white)"><svg width="18" height="18" viewBox="0 0 24 24"><path fill="#06248a" d="M6.6 10.8a15 15 0 006.6 6.6l2.2-2.2c.3-.3.7-.4 1-.2 1.1.4 2.3.6 3.6.6.6 0 1 .4 1 1V20c0 .6-.4 1-1 1A17 17 0 013 4c0-.6.4-1 1-1h3.5c.6 0 1 .4 1 1 0 1.3.2 2.5.6 3.6.1.3 0 .7-.2 1z"/></svg></span>
    <div><small style="color:#fff">Call Us:</small><strong style="color:#fff">(410) 555-0142</strong></div>
  </div>
  <nav class="abs nav" style="left:550px;top:5078px;font-size:14px">
    <span style="width:84px">Home</span><span style="width:142px">Work With Us</span><span style="width:128px">Work For Us</span><span style="width:108px">About Us</span><span>Contact Us</span>
  </nav>
  <p class="abs" style="left:846px;top:5130px;font-size:11px;color:var(--white)">(C) Copyright 2023 | All Rights Reserved.</p>
</footer>

</body>
</html>
```